Book Cover for Harbor Holiday Voyage Needed!

Marble Finch Press needs a cover for a novella. We will need an ebook cover and print wrap. We need to stay with the brand we have as indicated by the files attached. Take a look for the brand and style we are looking for.
Here are the specifics:
Title (subject to change): Seaside Wish
Subtitle: A Christmas Novella
Series Name: The Lagoon Pages Love Series (Book 3.5)
Author: Mira Calloway

Target Market(s)

Romance readers

Industry/Entity Type

Entertainment Industry

Font styles to use
Other font styles liked:
• NovitoNova - Title, Neumann - Subtitle

Colors
3276b5
33a6d7
33b8a4
abd036
fbee3d
ffc214

Requirements
Must have
• Please take a look at the other three covers to stay on brand and for inspiration
Nice to have
• Possibly something with a criuse ship.
Should not have
• Not looking for "real" images or depictions. We want a scene with bright colors same as the previous books but with a bit of a casual feel.

```html
<!DOCTYPE html>
<html lang="en">
<head>
<meta charset="utf-8">
<title>Seaside Wish — Book Cover</title>
<link rel="stylesheet" href="https://fonts.googleapis.com/css2?family=Big+Shoulders+Display:wght@100;200&family=Allura&family=Cinzel:wght@400&family=Cormorant+Garamond:wght@500&display=swap">
<style>
  :root {
    --page: #ffffff;
    --sky-deep: #1f8fcf;
    --sky-mid: #4cb6e4;
    --sky-glow: #c9eefa;
    --sea: #33b8d4;
    --sea-light: #8fdcea;
    --foam: #f4fbfd;
    --sand: #f6ecc9;
    --sand-deep: #eedcaa;
    --title: #ffffff;
    --title-shadow: #1d6aa8;
    --script: #2a5fa8;
    --author: #1d2f4f;
    --ribbon: #5fb7cf;
    --ribbon-edge: #d6b46a;
    --ribbon-text: #ffffff;
  }
  * { margin: 0; padding: 0; box-sizing: border-box; }
  html, body { width: 960px; height: 1200px; overflow: hidden; background: var(--page); }
  .canvas { position: relative; width: 960px; height: 1200px; }
  .cover {
    position: absolute; left: 193px; top: 142px; width: 574px; height: 915px;
    overflow: hidden;
  }
  .cover-scene {
    position: absolute; inset: 0;
    background:
      radial-gradient(ellipse 60% 35% at 50% 48%, var(--sky-glow) 0%, rgba(201,238,250,0) 70%),
      linear-gradient(to bottom,
        var(--sky-deep) 0%, var(--sky-mid) 30%, #8fd5f0 58%,
        var(--foam) 68%, var(--sea) 72%, var(--sea-light) 78%,
        var(--sand) 82%, var(--sand-deep) 100%);
  }
  .series-ribbon { position: absolute; left: 0; top: 0; width: 574px; height: 120px; }
  .series-ribbon text {
    font-family: "Cormorant Garamond", serif; font-weight: 500; font-size: 17px;
    fill: var(--ribbon-text);
  }
  .title { position: absolute; left: 0; top: 0; width: 574px; height: 915px; }
  .title text {
    font-family: "Big Shoulders Display", sans-serif; font-weight: 100;
    fill: var(--title); stroke: var(--title-shadow); stroke-width: 0.5;
  }
  .subtitle {
    position: absolute; left: 0; width: 574px; top: 618px; text-align: center;
    font-family: "Allura", cursive; font-size: 48px; color: var(--script);
    line-height: 1;
  }
  .author {
    position: absolute; left: 0; width: 574px; top: 800px; text-align: center;
    font-family: "Cinzel", serif; font-size: 36px; letter-spacing: 6px;
    color: var(--author); line-height: 1;
  }
</style>
</head>
<body>
<div class="canvas">
  <div class="cover">
    <div class="cover-scene" role="img" aria-label="Bright illustrated beach scene: palm fronds in the top corners, faint snowflakes in a blue sky, soft clouds over a turquoise sea with a small red cruise ship, and pale sand in the foreground"></div>

    <svg class="series-ribbon" viewBox="0 0 574 120" aria-label="The Lagoon Pages Love Series (Book 3.5)">
      <path d="M100 62 Q290 42 482 56 L482 88 Q290 74 100 94 Z" fill="var(--ribbon)" stroke="var(--ribbon-edge)" stroke-width="2.5"/>
      <path id="ribbon-line" d="M106 84 Q290 64 476 78" fill="none"/>
      <text><textPath href="#ribbon-line" startOffset="50%" text-anchor="middle">The Lagoon Pages Love Series (Book 3.5)</textPath></text>
    </svg>

    <svg class="title" viewBox="0 0 574 915" aria-label="Seaside Wish">
      <defs>
        <filter id="title-depth" x="-10%" y="-10%" width="120%" height="120%">
          <feDropShadow dx="2" dy="3" stdDeviation="1.5" flood-color="#1d6aa8" flood-opacity="0.75"/>
        </filter>
      </defs>
      <g filter="url(#title-depth)">
        <text x="99" y="296" font-size="173" textLength="393" lengthAdjust="spacingAndGlyphs">SEASIDE</text>
        <text x="99" y="558" font-size="308" textLength="393" lengthAdjust="spacingAndGlyphs">WISH</text>
      </g>
    </svg>

    <p class="subtitle">A Christmas Novella...</p>
    <p class="author">MIRA CALLOWAY</p>
  </div>
</div>
</body>
</html>
```